Website design for Puddle Jump Kidscare

I need a website designed for my daycare business, Puddle Jump Kidscare, now that I have a new logo. My former website was ok but simple and I did not have a logo yet. It also was created by me using a template and was entirely pink. I loved the bright, happy feel of it but worried it might not appeal as much to potential clients who have sons. Therefore, I need a site which will appeal to both genders while still keeping the cheerful color scheme of my new logo, which has pinks, blue, green and cream.
Updates

Reason: Hello! I am still trying to download my new logo and am sorry it is taking me so long. Hopefully I will it posted by the end of today (US Eastern Standard Time). Thank you all very much for your patience!

Hello! I have finally managed to upload my new logo for you to use in designing my website. I'm sorry it took so long and greatly appreciate your time and creative efforts! I look forward to seeing what is submitted based on my logo design and its style/colors.

Many thanks!

Reason: As I've been traveling and posted my logo file late, I am extending my deadline. I am now back and can focus on providing more and better feedback. I appreciate your patience and submissions very much!

Reason: I need more time to provide feedback and make decisions.

Industry/Entity Type

Daycare

Colors
0192cd
33a6d7
86cae7
cadf82
fbf289
add136
e34197

```html
<!DOCTYPE html>
<html lang="en">
<head>
<meta charset="utf-8">
<title>Puddle Jump Kidscare</title>
<link href="https://fonts.googleapis.com/css2?family=Open+Sans:wght@400;600;700&display=swap" rel="stylesheet">
<style>
  :root {
    --pink: #e34197;
    --blue: #0192cd;
    --blue-mid: #33a6d7;
    --blue-light: #86cae7;
    --green: #add136;
    --green-light: #cadf82;
    --yellow: #fbf289;
    --ink: #55555f;
    --muted: #9b9ba6;
    --nav: #a3a3ad;
    --white: #ffffff;
  }
  * { margin: 0; padding: 0; box-sizing: border-box; }
  html, body { width: 954px; height: 1200px; overflow: hidden; background: var(--white); }
  body { font-family: "Open Sans", Arial, sans-serif; position: relative; }

  .site-header { position: absolute; top: 0; left: 0; width: 954px; height: 175px; }
  .brand { position: absolute; top: 56px; left: 0; width: 954px; display: flex; justify-content: center; align-items: center; gap: 9px; }
  .brand-dot { width: 14px; height: 14px; border-radius: 50%; background: var(--blue-mid); }
  .brand-name { color: var(--pink); font-weight: 600; font-size: 24px; }

  .main-nav { position: absolute; top: 146px; left: 0; width: 954px; display: flex; justify-content: center; gap: 12px; }
  .main-nav a { font-size: 9.2px; text-transform: uppercase; color: var(--nav); text-decoration: none; }
  .main-nav a.active { color: var(--pink); }

  .hero { position: absolute; top: 175px; left: 0; width: 954px; height: 359px;
    background:
      radial-gradient(ellipse 190px 150px at 300px 60px, rgba(214,46,52,0.9), rgba(214,46,52,0) 100%),
      radial-gradient(ellipse 230px 170px at 700px 260px, rgba(227,65,151,0.95), rgba(227,65,151,0) 100%),
      radial-gradient(ellipse 200px 150px at 140px 300px, rgba(251,238,240,0.95), rgba(251,238,240,0) 100%),
      radial-gradient(ellipse 320px 220px at 470px 190px, #f1d2bd 0%, #e8bfa6 45%, rgba(232,191,166,0) 100%),
      linear-gradient(160deg, #4f8a2a 0%, #6fa03a 50%, #5b8f2c 100%); }
  .hero-arrow { position: absolute; top: 165px; }
  .hero-arrow.prev { left: 105px; }
  .hero-arrow.next { left: 822px; }
  .hero-dots { position: absolute; top: 341px; left: 376px; display: flex; gap: 2px; }
  .hero-dots span { width: 66px; height: 2px; background: rgba(255,255,255,0.4); }
  .hero-dots span.on { background: var(--white); }

  .welcome { position: absolute; top: 560px; left: 104px; width: 746px; text-align: center; }
  .welcome h1 { font-weight: 400; font-size: 14px; color: var(--ink); margin-bottom: 12px; }
  .welcome p { font-size: 9.2px; line-height: 15.4px; color: var(--muted); }
  .welcome p + p { margin-top: 15px; }

  .features { position: absolute; top: 699px; left: 0; width: 954px; height: 209px;
    background: linear-gradient(180deg, var(--blue-mid) 0%, var(--blue) 100%); }
  .feature { position: absolute; top: 16px; width: 232px; text-align: center; color: var(--white); }
  .feature .icon { display: block; margin: 0 auto; }
  .feature h2 { font-size: 12px; font-weight: 600; margin-top: 6px; }
  .feature p { font-size: 9.2px; font-weight: 600; line-height: 15.3px; margin-top: 7px; }
  .f-learning { left: 106px; }
  .f-creativity { left: 361px; }
  .f-sharing { left: 615px; }

  .news { position: absolute; top: 940px; left: 105px; width: 744px; text-align: center; }
  .news h2 { font-size: 14px; font-weight: 400; color: var(--ink); margin-bottom: 14px; }
  .news p { font-size: 9.2px; line-height: 15.4px; color: var(--muted); }
  .news-date { display: flex; align-items: center; gap: 10px; margin-top: 7px; font-size: 8.2px; color: var(--ink); }
  .news-date::before, .news-date::after { content: ""; flex: 1; height: 1px; background: var(--blue-mid); }

  .site-footer { position: absolute; top: 1073px; left: 0; width: 954px; height: 127px; background: var(--green); }
  .footer-brand { position: absolute; top: 52px; left: 105px; display: flex; align-items: center; gap: 6px; }
  .footer-brand .brand-dot { width: 11px; height: 11px; background: var(--blue); }
  .footer-brand .brand-name { font-size: 17px; }
  .footer-nav { position: absolute; top: 57px; right: 104px; display: flex; gap: 11px; }
  .footer-nav a { font-size: 9px; font-weight: 600; color: var(--white); text-decoration: none; text-transform: uppercase; }
  .copyright { position: absolute; top: 103px; right: 104px; font-size: 8.2px; color: var(--white); }
</style>
</head>
<body>
  <header class="site-header">
    <div class="brand"><span class="brand-dot"></span><span class="brand-name">Puddle Jump Kidscare</span></div>
    <nav class="main-nav">
      <a class="active" href="#">Home</a><a href="#">About Us</a><a href="#">Services</a><a href="#">Hours and Fees</a><a href="#">Policies</a><a href="#">Contact Us</a><a href="#">Photos</a><a href="#">Testimonials</a>
    </nav>
  </header>

  <section class="hero" role="img" aria-label="Photo of smiling children lying on grass in a circle, waving">
    <svg class="hero-arrow prev" width="27" height="27" viewBox="0 0 27 27"><circle cx="13.5" cy="13.5" r="13.5" fill="rgba(120,120,120,0.6)"/><path d="M15.5 8 L10 13.5 L15.5 19" stroke="#fff" stroke-width="2.4" fill="none" stroke-linecap="round"/></svg>
    <svg class="hero-arrow next" width="27" height="27" viewBox="0 0 27 27"><circle cx="13.5" cy="13.5" r="13.5" fill="rgba(120,120,120,0.6)"/><path d="M11.5 8 L17 13.5 L11.5 19" stroke="#fff" stroke-width="2.4" fill="none" stroke-linecap="round"/></svg>
    <div class="hero-dots"><span class="on"></span><span></span><span></span></div>
  </section>

  <section class="welcome">
    <h1>Welcome to Puddle Jump Kidscare, a playspace where children can play, create, and imagine!</h1>
    <p>Welcome to Puddle Jump Kidscare, a licensed Group Family Day Care, located in Maple Harbor's lovely Brookside district. We are located on a pretty, tree-lined block on Linden Street, between Oak and Elm Avenues. We are a few blocks from the Green line tram and the Harbor Road bus route, and we offer flexible hourly childcare, making it as easy as possible for busy parents on the go to arrange their children's care.</p>
    <p>We invite you to learn more about us and hope you will visit us soon!</p>
  </section>

  <section class="features">
    <div class="feature f-learning">
      <svg class="icon" width="60" height="60" viewBox="0 0 60 60" aria-hidden="true">
        <circle cx="30" cy="30" r="29" fill="#fbf289"/>
        <rect x="14" y="16" width="32" height="22" rx="2" fill="#add136" stroke="#5c7a1c" stroke-width="2"/>
        <path d="M20 38 L16 48 M40 38 L44 48" stroke="#5c7a1c" stroke-width="2.4" stroke-linecap="round"/>
        <path d="M19 24 H33 M19 30 H28" stroke="#fff" stroke-width="2" stroke-linecap="round"/>
      </svg>
      <h2>Learning</h2>
      <p>We develop age-appropriate activities that introduce and strengthen academic and social skills.</p>
    </div>
    <div class="feature f-creativity">
      <svg class="icon" width="60" height="60" viewBox="0 0 60 60" aria-hidden="true">
        <circle cx="30" cy="30" r="29" fill="#fbf289"/>
        <ellipse cx="30" cy="31" rx="17" ry="14" fill="#fff" stroke="#0192cd" stroke-width="2"/>
        <circle cx="23" cy="26" r="3" fill="#e34197"/>
        <circle cx="31" cy="23" r="3" fill="#0192cd"/>
        <circle cx="39" cy="27" r="3" fill="#add136"/>
        <circle cx="25" cy="36" r="3" fill="#33a6d7"/>
        <circle cx="36" cy="37" r="3.2" fill="#fbf289" stroke="#0192cd" stroke-width="1.4"/>
      </svg>
      <h2>Creativity</h2>
      <p>We offer children a wide range of creative opportunities including art projects, toddler yoga lessons, afternoon tea parties, dress up play, and a large selection of books and games.</p>
    </div>
    <div class="feature f-sharing">
      <svg class="icon" width="60" height="60" viewBox="0 0 60 60" aria-hidden="true">
        <circle cx="30" cy="30" r="29" fill="#fbf289"/>
        <rect x="17" y="26" width="26" height="20" rx="2" fill="#e34197"/>
        <rect x="15" y="20" width="30" height="7" rx="2" fill="#e34197"/>
        <rect x="28" y="20" width="4" height="26" fill="#86cae7"/>
        <path d="M30 20 C24 12 18 16 24 20 M30 20 C36 12 42 16 36 20" stroke="#0192cd" stroke-width="2.2" fill="none" stroke-linecap="round"/>
      </svg>
      <h2>Sharing</h2>
      <p>We strive to include enrichment activities that extend your child's understanding of the world and their role in it. During our tea parties, for instance, we teach and emphasize good manners so that your child can learn their benefits as they grow.</p>
    </div>
  </section>

  <section class="news">
    <h2>News</h2>
    <p>We are thrilled to have found a new cheerful space with a private backyard! It's large, sunny, and filled with outdoor play equipment such as a toddler slide, sand/water activity table, and lots of toys! Please stay tuned for updates on our program and services as we say goodbye to Winter and hello to Spring!</p>
    <div class="news-date">March 10, 2014</div>
  </section>

  <footer class="site-footer">
    <div class="footer-brand"><span class="brand-dot"></span><span class="brand-name">Puddle Jump Kidscare</span></div>
    <nav class="footer-nav">
      <a href="#">Home</a><a href="#">About Us</a><a href="#">Services</a><a href="#">Hours and Fees</a><a href="#">Policies</a><a href="#">Contact Us</a><a href="#">Photos</a><a href="#">Testimonials</a>
    </nav>
    <div class="copyright">Copyright PuddleJumpKidscare 2014. All Rights Reserved</div>
  </footer>
</body>
</html>
```